Meridale Partners Website

Meridale Partners (MP) provide Analytics & Enterprise Performance Management (EPM) advisory & consultancy services. We are passionate about data and making a difference for our clients by working in partnership with them, helping them on their journey to becoming an Meridale Partner. We deliver insights which give our clients a competitive edge and a much deeper understanding of their organisation.

We need a website which shows who we are, what we do and how we do it.

www.meridale-partners.example is our very basic website at the moment. We want to completely revamp it with a corporate look

```html
<!DOCTYPE html>
<html lang="en">
<head>
<meta charset="utf-8">
<title>Meridale Partners</title>
<link href="https://fonts.googleapis.com/css2?family=Roboto:wght@400;500;700&family=Montserrat:wght@400;500&family=Tinos&display=swap" rel="stylesheet">
<style>
:root{
  --navy:#0f4369;
  --blue:#1d5679;
  --slate:#2c5672;
  --orange:#e69558;
  --orange-line:#e08a4a;
  --grey-leaf:#d9d9d9;
  --white:#ffffff;
  --ink:#111111;
}
*{box-sizing:border-box;margin:0;padding:0}
html,body{width:1200px;height:2992px;overflow:hidden}
body{position:relative;font-family:"Roboto",sans-serif;color:var(--ink);background:var(--white)}
.abs{position:absolute}
.center{left:0;width:1200px;text-align:center}

/* header + hero */
.hero{position:absolute;left:0;top:0;width:1200px;height:686px;background:linear-gradient(160deg,#4a6c8f 0%,#3a5d7f 40%,#2c4f6e 75%,#35566f 100%)}
.hero-photo{position:absolute;inset:0;background:radial-gradient(ellipse at 30% 30%,rgba(140,165,190,.35),transparent 60%),radial-gradient(ellipse at 80% 70%,rgba(30,60,90,.45),transparent 60%)}
.site-header{position:absolute;left:0;top:0;width:1200px;height:82px;border-bottom:1px solid rgba(255,255,255,.55)}
.brand{position:absolute;left:98px;top:22px;display:flex;align-items:center;gap:10px;color:var(--white);font:700 17px/1.1 "Roboto",sans-serif;letter-spacing:.5px}
.brand-dot{width:34px;height:34px;border-radius:50%;border:4px solid var(--white)}
.main-nav a{position:absolute;top:0;height:82px;line-height:84px;text-align:center;color:var(--white);font-size:15px;text-decoration:none;border-left:1px solid rgba(255,255,255,.55)}
.hero-frame-h{left:0;top:263px;width:146px;height:1px;background:var(--white)}
.hero-frame-v{left:145px;top:263px;width:1px;height:24px;background:var(--white)}
.hero-kicker{left:154px;top:263px;color:var(--white);font-size:15px}
.hero-title{left:154px;top:286px;color:var(--white);font:700 52px/1.2 "Roboto",sans-serif}
.hero-sub{left:155px;top:349px;color:var(--white);font-size:20px}
.btn{display:block;border:2px solid var(--white);color:var(--white);text-align:center;font-size:17px;text-decoration:none}
.hero-btn{left:158px;top:401px;width:147px;height:44px;line-height:40px}

.connector{position:absolute;left:599px;width:1px}
.connector::after{content:"";position:absolute;left:-18px;bottom:0;width:37px;height:1px;background:inherit}

/* who */
.who{position:absolute;left:0;top:686px;width:1200px;height:492px;background:var(--blue)}
.kicker{font-size:20px}
.section-title{font:700 48px/1 "Roboto",sans-serif}
.who-text{left:160px;width:880px;top:889px;color:var(--white);font-size:18px;line-height:34px;text-align:center}
.who-call{top:1005px;color:var(--white);font-size:21px;font-weight:500}
.who-btn{left:526px;top:1066px;width:147px;height:45px;line-height:41px}

/* services */
.service-card{position:absolute;top:1410px;width:313px;height:581px;border:1.5px solid var(--orange-line);border-radius:157px;text-align:center}
.service-card.featured{background:var(--slate);border-color:var(--slate);box-shadow:0 12px 18px rgba(0,0,0,.22);color:var(--white)}
.service-photo{position:absolute;left:37px;top:19px;width:240px;height:240px;border-radius:50%}
.service-title{position:absolute;left:0;width:100%;top:268px;font:500 22px/29px "Roboto",sans-serif;padding:0 6px}
.service-text{position:absolute;left:18px;width:275px;font:400 16.5px/26px "Montserrat",sans-serif}
.arrow-icon{position:absolute;left:143px;top:512px;width:27px;height:27px}

/* how */
.how{position:absolute;left:0;top:2134px;width:1200px;height:480px;background:var(--orange)}
.step{position:absolute;top:2324px;width:230px;text-align:center;color:var(--white)}
.leaf{display:block;margin:0 auto;width:122px;height:72px}
.step-title{margin-top:23px;font:500 21px/1 "Roboto",sans-serif}
.step-text{margin-top:12px;font:13.5px/22px "Tinos",serif}
.step-btn{margin:15px auto 0;width:105px;height:31px;line-height:28px;font-size:12px;border-width:1.5px}

/* footer */
.site-footer{position:absolute;left:0;top:2614px;width:1200px;height:378px;background:var(--navy);color:var(--white)}
.footer-brand{position:absolute;left:122px;top:120px;display:flex;align-items:center;gap:14px;font:700 26px/1.15 "Roboto",sans-serif}
.footer-brand .brand-dot{width:58px;height:58px;border-width:7px}
.footer-col h3{position:absolute;top:66px;font:500 16px/1 "Roboto",sans-serif}
.footer-col ul{position:absolute;top:130px;list-style:none;font-size:15px;line-height:26px}
.help ul{line-height:34.5px;top:122px}
.footer-divider{position:absolute;top:58px;width:1.5px;height:200px;background:#e0a23a}
.loc-row{position:absolute;left:824px;display:flex;align-items:flex-start;gap:14px;font-size:15px;line-height:26px}
.loc-icon{width:30px;height:30px;flex:none}
.footer-rule{position:absolute;left:99px;top:304px;width:999px;height:1px;background:rgba(255,255,255,.5)}
.copyright{position:absolute;left:0;width:1200px;top:334px;text-align:center;font-size:15px}
</style>
</head>
<body>

<section class="hero">
  <div class="hero-photo" role="img" aria-label="Photo of a glass office building against a cloudy sky"></div>
  <header class="site-header">
    <div class="brand"><span class="brand-dot"></span><span>MERIDALE<br>PARTNERS</span></div>
    <nav class="main-nav">
      <a style="left:489px;width:113px">Home</a>
      <a style="left:602px;width:121px">About Us</a>
      <a style="left:723px;width:118px">Services</a>
      <a style="left:841px;width:152px">How Its Work</a>
      <a style="left:993px;width:139px">Contact Us</a>
      <a style="left:1132px;width:1px"></a>
    </nav>
  </header>
  <div class="abs hero-frame-h"></div>
  <div class="abs hero-frame-v"></div>
  <p class="abs hero-kicker">WELCOME TO MERIDALE PARTNERS</p>
  <h1 class="abs hero-title">MERIDALE PARTNERS</h1>
  <p class="abs hero-sub">Data Analytics &amp; Epm Consulting Services</p>
  <a class="abs btn hero-btn">CONTACT US</a>
</section>
<div class="connector" style="top:631px;height:132px;background:var(--white)"></div>

<section class="who"></section>
<p class="abs center kicker" style="top:778px;color:var(--white)">who we are</p>
<h2 class="abs center section-title" style="top:818px;color:var(--white)">MERIDALE PARTNERS</h2>
<p class="abs who-text">Meridale Partners is an exciting start-up in the Data Analytics and EPM space.&nbsp; Founded in 2019, MP specialise in the implementation and support of BI, EPM and Data Analytics business solutions, both in the Cloud and on-premise.</p>
<p class="abs center who-call">Call us on 01 555 0148 or email: info@meridale-partners.example for more information</p>
<a class="abs btn who-btn">READ MORE</a>

<div class="connector" style="top:1178px;height:82px;background:var(--navy)"></div>
<p class="abs center kicker" style="top:1278px;color:var(--blue)">what we do</p>
<h2 class="abs center section-title" style="top:1316px">OUR SERVICES</h2>

<article class="service-card" style="left:99px">
  <div class="service-photo" role="img" aria-label="Photo of two colleagues talking in an office corridor" style="background:linear-gradient(135deg,#8a7a6a,#4a4036 60%,#2d2a28)"></div>
  <h3 class="service-title">Meridale Partners</h3>
  <p class="service-text" style="top:350px">Lorem ipsum dolor sit amet, consectetur adipiscing elit, sed do eiusmod tempor incididunt ut labore et dolore magna aliqua. Ut enim ad minim veniam, quis nostrud exercitation ullamco</p>
  <svg class="arrow-icon" viewBox="0 0 28 28"><circle cx="14" cy="14" r="13" fill="var(--orange-line)"/><path d="M7 14h12M14 8l6 6-6 6" stroke="#fff" stroke-width="3" fill="none"/></svg>
</article>

<article class="service-card featured" style="left:443px">
  <div class="service-photo" role="img" aria-label="Photo of a consultant wearing glasses in a dark office" style="background:linear-gradient(135deg,#f4f4f4 0%,#dfe4ea 40%,#2c3a4a 70%,#1b2530)"></div>
  <h3 class="service-title">Provide Analytics &amp; Enterprise Performance Management</h3>
  <p class="service-text" style="top:356px">Lorem ipsum dolor sit amet, consectetur adipiscing elit, sed do eiusmod tempor incididunt ut labore et dolore magna aliqua. Ut enim ad minim veniam, quis nostrud</p>
  <svg class="arrow-icon" viewBox="0 0 28 28"><circle cx="14" cy="14" r="13" fill="var(--orange-line)"/><path d="M7 14h12M14 8l6 6-6 6" stroke="#fff" stroke-width="3" fill="none"/></svg>
</article>

<article class="service-card" style="left:785px">
  <div class="service-photo" role="img" aria-label="Photo of an advisor in a purple shirt meeting a client" style="background:linear-gradient(135deg,#e6e4e0,#8e86b0 55%,#5a4a6a)"></div>
  <h3 class="service-title">Advisory &amp; Consultancy</h3>
  <p class="service-text" style="top:357px">Lorem ipsum dolor sit amet, consectetur adipiscing elit, sed do eiusmod tempor incididunt ut labore et dolore magna aliqua. Ut enim ad minim veniam, quis nostrud exercitation ullamco</p>
  <svg class="arrow-icon" viewBox="0 0 28 28"><circle cx="14" cy="14" r="13" fill="var(--orange-line)"/><path d="M7 14h12M14 8l6 6-6 6" stroke="#fff" stroke-width="3" fill="none"/></svg>
</article>

<section class="how"></section>
<div class="connector" style="top:2053px;height:131px;background:#6a7a88"></div>
<p class="abs center kicker" style="top:2201px;color:var(--white)">How we do it</p>
<h2 class="abs center section-title" style="top:2246px;color:var(--white);font-weight:500">HOW ITS WORK</h2>

<div class="step" style="left:91px">
  <svg class="leaf" viewBox="0 0 122 72"><path d="M0 22C30-8 92-6 122 50C92 80 30 78 0 22Z" fill="var(--grey-leaf)"/><g stroke="#666" stroke-width="2" fill="none"><circle cx="52" cy="30" r="6"/><circle cx="68" cy="30" r="6"/><path d="M42 54v-8a10 10 0 0 1 20 0v8M58 54v-8a10 10 0 0 1 20 0v8"/></g></svg>
  <h3 class="step-title">LOREM</h3>
  <p class="step-text">Lorem ipsum dolor sit amet, consectetur adipiscing elit, sed do eiusmod tempor.</p>
  <a class="btn step-btn">READ MORE</a>
</div>
<div class="step" style="left:351px">
  <svg class="leaf" viewBox="0 0 122 72"><path d="M0 22C30-8 92-6 122 50C92 80 30 78 0 22Z" fill="var(--navy)"/><g stroke="#fff" stroke-width="2" fill="none"><path d="M32 30l12-6 14 8 10-8 14 6M32 30l16 16 8 4 16-10 10-10M50 40l6 6M56 36l8 8"/></g></svg>
  <h3 class="step-title">LOREM</h3>
  <p class="step-text">Lorem ipsum dolor sit amet, consectetur adipiscing elit, sed do eiusmod tempor.</p>
  <a class="btn step-btn">READ MORE</a>
</div>
<div class="step" style="left:611px">
  <svg class="leaf" viewBox="0 0 122 72"><path d="M0 22C30-8 92-6 122 50C92 80 30 78 0 22Z" fill="var(--grey-leaf)"/><g stroke="#666" stroke-width="2" fill="none"><circle cx="58" cy="28" r="7"/><circle cx="58" cy="28" r="2"/><path d="M40 50h12l10-4h10M40 56h34l10-8"/></g></svg>
  <h3 class="step-title">LOREM</h3>
  <p class="step-text">Lorem ipsum dolor sit amet, consectetur adipiscing elit, sed do eiusmod tempor.</p>
  <a class="btn step-btn">READ MORE</a>
</div>
<div class="step" style="left:871px">
  <svg class="leaf" viewBox="0 0 122 72"><path d="M0 22C30-8 92-6 122 50C92 80 30 78 0 22Z" fill="var(--grey-leaf)"/><g stroke="#666" stroke-width="2" fill="none"><path d="M44 54h34M48 54v-8h5v8M56 54v-12h5v12M64 54v-16h5v16M72 54v-22h5v22M46 40l12-8 8 4 12-10"/></g></svg>
  <h3 class="step-title">LOREM</h3>
  <p class="step-text">Lorem ipsum dolor sit amet, consectetur adipiscing elit, sed do eiusmod tempor.</p>
  <a class="btn step-btn">READ MORE</a>
</div>

<footer class="site-footer">
  <div class="footer-brand"><span class="brand-dot"></span><span>MERIDALE<br>PARTNERS</span></div>
  <div class="footer-col">
    <h3 style="left:411px">QUICK LINKS</h3>
    <ul style="left:411px"><li>Home</li><li>About Us</li><li>Services</li><li>How Its Work</li><li>Contact Us</li></ul>
  </div>
  <div class="footer-divider" style="left:553px"></div>
  <div class="footer-col help">
    <h3 style="left:611px">HELP LINK</h3>
    <ul style="left:611px"><li>Terms &amp; Conditions</li><li>Privacy Policy</li><li>About Us</li><li>Support</li></ul>
  </div>
  <div class="footer-divider" style="left:778px"></div>
  <div class="footer-col"><h3 style="left:824px;top:64px">OUR LOCATION</h3></div>
  <div class="loc-row" style="top:124px">
    <svg class="loc-icon" viewBox="0 0 30 30"><circle cx="15" cy="15" r="14" stroke="#fff" stroke-width="1.5" fill="none"/><path d="M15 22s-5-5-5-9a5 5 0 0 1 10 0c0 4-5 9-5 9z" stroke="#fff" stroke-width="1.5" fill="none"/><circle cx="15" cy="13" r="1.6" fill="#fff"/></svg>
    <span>14 Harbour Row, Eastgate<br>Dublin 4, D04 K2X7</span>
  </div>
  <div class="loc-row" style="top:192px">
    <svg class="loc-icon" viewBox="0 0 30 30"><circle cx="15" cy="15" r="14" stroke="#fff" stroke-width="1.5" fill="none"/><path d="M10 9l3 0 1 4-2 1a9 9 0 0 0 4 4l1-2 4 1 0 3c-7 1-12-4-11-11z" stroke="#fff" stroke-width="1.4" fill="none"/></svg>
    <span>+1 01 555 0148</span>
  </div>
  <div class="loc-row" style="top:250px;font-size:18px">
    <svg class="loc-icon" viewBox="0 0 30 30"><circle cx="15" cy="15" r="14" stroke="#fff" stroke-width="1.5" fill="none"/><rect x="8.5" y="10" width="13" height="10" rx="1.5" stroke="#fff" stroke-width="1.4" fill="none"/><path d="M9 11l6 5 6-5" stroke="#fff" stroke-width="1.4" fill="none"/></svg>
    <span>info@meridale-partner</span>
  </div>
  <div class="footer-rule"></div>
  <p class="copyright">© copyrights 2022 &nbsp;Meridale-Partners &nbsp;| &nbsp;All Rights Reserved</p>
</footer>

</body>
</html>
```